Design a compelling Tarnwove Business Card that will drive people to my site

I want a business card that I can give to people—less to tell them who I am and more to direct them to my website. My website is a portal for Pelmor Aquatics Officials and a place for people who want to become Pelmor Aquatics Officials.
I am uploading my official company logo as well as a business card mockup that I did on my own. Please feel free to completely stray from this design.
I've included a screen recording of the homepage of my website as well.
Target Market(s)
Pelmor Aquatics Officials and people who desire to become one
Contact Information for Business Card
website url
Look and feel
Each slider illustrates characteristics of the customer's brand and the style your logo design should communicate.

```html
<!DOCTYPE html>
<html lang="en">
<head>
<meta charset="utf-8">
<title>Tarnwove Business Card</title>
<link rel="stylesheet" href="https://fonts.googleapis.com/css2?family=Montserrat:wght@400;600&display=swap">
<style>
  :root {
    --brand-blue: #3a54a8;
    --brand-blue-deep: #33499a;
    --soft-blue: #9aaee0;
    --card-white: #ffffff;
    --table-grey: #e9eaec;
    --shadow: rgba(20, 24, 40, 0.28);
  }
  * { box-sizing: border-box; margin: 0; padding: 0; }
  html, body { width: 1200px; height: 915px; overflow: hidden; }
  body {
    background: var(--table-grey);
    font-family: "Montserrat", sans-serif;
    position: relative;
  }
  .card {
    position: absolute;
    width: 540px;
    height: 308px;
    border-radius: 22px;
    overflow: hidden;
    box-shadow: 0 14px 30px var(--shadow);
    background: var(--brand-blue);
  }
  .card--front { left: 70px; top: 100px; }
  .card--back { left: 590px; top: 500px; }

  .card__texture {
    position: absolute; inset: 0;
    background:
      radial-gradient(circle at 78% 22%, rgba(255,255,255,0.12), transparent 22%),
      radial-gradient(circle at 20% 70%, rgba(255,255,255,0.08), transparent 18%),
      radial-gradient(circle at 55% 85%, rgba(255,255,255,0.09), transparent 16%),
      var(--brand-blue);
  }
  .brand {
    position: absolute;
    display: flex; align-items: center; gap: 12px;
    color: var(--card-white);
    font-weight: 600;
    letter-spacing: -1px;
    line-height: 1;
  }
  .brand__dot {
    width: 22px; height: 22px; border-radius: 50%;
    background: var(--card-white);
  }
  .card--front .brand { left: 50%; top: 50%; transform: translate(-50%, -50%); font-size: 64px; }

  .card__split { position: absolute; inset: 0; width: 100%; height: 100%; }
  .card--back .brand { left: 30px; bottom: 30px; font-size: 46px; }
  .card--back .brand__dot { width: 16px; height: 16px; }

  .contact {
    position: absolute; right: 30px; top: 138px;
    text-align: right; color: var(--card-white);
  }
  .contact__name { font-weight: 600; font-size: 17px; color: var(--soft-blue); }
  .contact__role { font-size: 12px; margin-top: 3px; }
  .contact__rule { width: 18px; height: 1px; background: var(--soft-blue); margin: 8px 0 8px auto; }
  .contact__list { list-style: none; font-size: 12.5px; }
  .contact__list li { display: flex; align-items: center; justify-content: flex-end; gap: 8px; margin-bottom: 6px; }
  .contact__list svg { width: 12px; height: 12px; flex: none; }
</style>
</head>
<body>
  <section class="card card--front">
    <div class="card__texture" role="img" aria-label="Soft floating bubble pattern in brand blue"></div>
    <div class="brand"><span class="brand__dot"></span>tarnwove</div>
  </section>

  <section class="card card--back">
    <svg class="card__split" viewBox="0 0 540 308" preserveAspectRatio="none" aria-hidden="true">
      <rect width="540" height="308" fill="var(--brand-blue)"/>
      <path d="M0 0 H540 V70 C420 95 330 150 250 190 C170 225 80 230 0 215 Z" fill="var(--card-white)"/>
    </svg>
    <div class="brand"><span class="brand__dot"></span>tarnwove</div>
    <div class="contact">
      <p class="contact__name">Marcus Ellery</p>
      <p class="contact__role">CEO &amp; Founder</p>
      <div class="contact__rule"></div>
      <ul class="contact__list">
        <li>(555) 201-4478
          <svg viewBox="0 0 24 24"><path fill="#fff" d="M6.6 10.8a15 15 0 0 0 6.6 6.6l2.2-2.2c.3-.3.7-.4 1-.2 1.1.4 2.3.6 3.6.6.6 0 1 .4 1 1V20c0 .6-.4 1-1 1A17 17 0 0 1 3 4c0-.6.4-1 1-1h3.5c.6 0 1 .4 1 1 0 1.3.2 2.5.6 3.6.1.3 0 .7-.2 1z"/></svg>
        </li>
        <li>marcus@tarnwove.com
          <svg viewBox="0 0 24 24"><rect x="2" y="5" width="20" height="14" rx="2" fill="#fff"/><path d="M3 6l9 7 9-7" stroke="var(--brand-blue)" stroke-width="1.6" fill="none"/></svg>
        </li>
        <li>www.tarnwove.com
          <svg viewBox="0 0 24 24"><circle cx="12" cy="12" r="9" fill="none" stroke="#fff" stroke-width="2"/><path d="M3 12h18M12 3c3 3 3 15 0 18M12 3c-3 3-3 15 0 18" stroke="#fff" stroke-width="1.5" fill="none"/></svg>
        </li>
      </ul>
    </div>
  </section>
</body>
</html>
```